World Wide News and Current Affairs website

We intends to start up a new website which deals on New and Current Affairs.
Attention Designers,
We want a home page design for this project. Our business is based in the United States. Our goal is to become a well known brand.
The website would consist of a category for News, Business and Tech.
The theme should be beautiful and attention seeking. The website would take bulk of it's news from the US, and Europe.
Designers can get inspiration from already existing new websites such as PWJ, KLV, DASKOLM.
All designs should be clean and easy to navigate.

```html
<!DOCTYPE html>
<html lang="en">
<head>
<meta charset="utf-8">
<title>Tidewell News</title>
<link rel="stylesheet" href="https://fonts.googleapis.com/css2?family=Nunito+Sans:wght@400;600;700;800&family=Open+Sans:wght@400;600&display=swap">
<style>
:root{
  --accent:#1ea3d8;
  --ink:#1d1f24;
  --muted:#8a8f96;
  --rule:#e3e5e8;
  --white:#ffffff;
  --footer-bg:#ffffff;
  --icon:#5b7186;
}
*{box-sizing:border-box;margin:0;padding:0}
html,body{width:1200px;height:3396px;overflow:hidden;background:var(--white)}
body{position:relative;font-family:"Open Sans",Arial,sans-serif;color:var(--ink)}

/* Hero */
.hero{position:absolute;left:0;top:0;width:1200px;height:516px;overflow:hidden}
.hero-photo{position:absolute;inset:0;background:linear-gradient(100deg,#5c6878 0%,#8a96a4 35%,#c9cdd2 55%,#7d8894 75%,#3b4a5e 100%)}
.hero-shade{position:absolute;inset:0;background:linear-gradient(90deg,rgba(20,28,40,.72) 0%,rgba(20,28,40,.35) 55%,rgba(20,28,40,.1) 100%)}
.topbar{position:absolute;left:100px;top:0;width:1000px;height:80px;display:flex;align-items:center;justify-content:space-between}
.hero::after{content:"";position:absolute;left:0;right:0;top:80px;height:1px;background:rgba(255,255,255,.3)}
.brand{font-family:"Nunito Sans",Arial,sans-serif;font-weight:800;font-size:20px;color:var(--white);letter-spacing:.3px}
.nav{display:flex;align-items:center;gap:24px;font-family:"Nunito Sans",Arial,sans-serif;font-weight:700;font-size:13px;color:var(--white)}
.nav .active{color:var(--accent)}
.signin{display:flex;align-items:center;gap:6px;border:1.5px solid var(--white);border-radius:16px;padding:6px 14px}
.hero-copy{position:absolute;left:100px;top:186px;width:620px;color:var(--white)}
.hero-kicker{font-family:"Nunito Sans",Arial,sans-serif;font-weight:800;font-size:15px;letter-spacing:.3px}
.hero-title{font-family:"Nunito Sans",Arial,sans-serif;font-weight:800;font-size:36px;margin-top:18px;letter-spacing:.3px}
.hero-text{font-size:14px;line-height:25px;margin-top:14px}
.hero-btn{display:inline-block;margin-top:26px;width:178px;height:40px;line-height:36px;text-align:center;background:var(--accent);border:2px solid var(--white);border-radius:20px;font-family:"Nunito Sans",Arial,sans-serif;font-weight:800;font-size:14px}
.dots{position:absolute;left:557px;top:450px;display:flex;gap:6px}
.dots span{width:14px;height:14px;border-radius:50%;border:2px solid var(--white)}
.dots span.on{background:var(--white)}

/* Sections */
.section{position:absolute;left:100px;width:1000px}
.section-title{font-family:"Nunito Sans",Arial,sans-serif;font-weight:800;font-size:22px;letter-spacing:.3px;padding-bottom:20px;border-bottom:1px solid var(--rule)}
.section-body{position:relative;margin-top:30px;height:401px}
.lead{position:absolute;left:0;top:0;width:525px;height:401px;border:4px solid var(--white);box-shadow:0 0 0 1px var(--rule),0 2px 6px rgba(0,0,0,.12);overflow:hidden}
.lead-photo{position:absolute;inset:0}
.lead-shade{position:absolute;left:0;right:0;bottom:0;height:195px;background:linear-gradient(180deg,rgba(10,15,25,0) 0%,rgba(10,15,25,.55) 30%,rgba(10,15,25,.75) 100%)}
.lead-copy{position:absolute;left:26px;right:26px;top:223px;color:var(--white)}
.lead-kicker{font-family:"Nunito Sans",Arial,sans-serif;font-weight:800;font-size:12px}
.lead-title{font-family:"Nunito Sans",Arial,sans-serif;font-weight:800;font-size:21px;margin-top:14px}
.lead-text{font-size:12px;line-height:22px;margin-top:10px}
.meta{display:flex;align-items:center;gap:8px;font-size:11.5px;color:var(--muted);margin-top:12px}
.lead .meta{color:var(--white);margin-top:14px}
.meta .sep{opacity:.8}
.meta svg{width:11px;height:11px;fill:var(--accent)}

.list{position:absolute;left:572px;top:0;width:428px}
.item{position:relative;height:145px}
.thumb{position:absolute;left:0;top:0;width:134px;height:110px;border:4px solid var(--white);box-shadow:0 0 0 1px var(--rule),0 2px 5px rgba(0,0,0,.12);overflow:hidden}
.thumb-photo{position:absolute;inset:0}
.item-copy{position:absolute;left:159px;top:2px;width:269px}
.item-kicker{font-family:"Nunito Sans",Arial,sans-serif;font-weight:700;font-size:11px;color:var(--accent);text-transform:uppercase}
.item-title{font-family:"Nunito Sans",Arial,sans-serif;font-weight:700;font-size:16.5px;line-height:25px;margin-top:6px}
.item .meta{margin-top:10px}

.play{position:absolute;left:50%;top:50%;transform:translate(-50%,-50%)}

/* Banners */
.banner{position:absolute;left:0;width:1200px;height:224px;overflow:hidden}
.banner-photo{position:absolute;inset:0}
.banner-shade{position:absolute;inset:0;background:rgba(30,40,55,.28)}
.banner-text{position:absolute;left:0;right:0;top:68px;text-align:center;color:var(--white);font-family:"Nunito Sans",Arial,sans-serif;font-weight:700;font-size:25px;line-height:43px}

/* Footer */
.footer{position:absolute;left:0;top:3034px;width:1200px;height:362px;background:var(--footer-bg)}
.fcol{position:absolute;top:66px}
.fcol h4{font-family:"Nunito Sans",Arial,sans-serif;font-weight:800;font-size:16px;color:var(--ink)}
.fcol ul{list-style:none;margin-top:13px}
.fcol li{font-size:11.5px;color:#5a5f66;line-height:28px}
.subscribe p{font-size:11.5px;color:#5a5f66;margin-top:16px}
.sub-form{display:flex;margin-top:14px;width:323px;height:34px;border:1px solid var(--rule)}
.sub-input{flex:1;font-size:11.5px;color:var(--muted);padding:9px 12px}
.sub-btn{width:93px;background:var(--accent);color:var(--white);font-family:"Nunito Sans",Arial,sans-serif;font-weight:800;font-size:12px;text-align:center;line-height:34px}
.connect{font-family:"Nunito Sans",Arial,sans-serif;font-weight:800;font-size:16px;margin-top:28px}
.socials{display:flex;gap:8px;margin-top:12px}
.socials span{width:34px;height:34px;border-radius:50%;background:var(--icon)}
.footer-rule{position:absolute;left:100px;width:1000px;top:289px;height:1px;background:var(--rule)}
.copyright{position:absolute;left:0;right:0;top:317px;text-align:center;font-size:11.5px;color:#5a5f66}
</style>
</head>
<body>

<header class="hero">
  <div class="hero-photo" role="img" aria-label="Business team seated at a meeting table"></div>
  <div class="hero-shade"></div>
  <div class="topbar">
    <div class="brand">TIDEWELL NEWS</div>
    <nav class="nav">
      <span class="active">HOME</span><span>NEWS</span><span>BUSINESS</span><span>TECH</span><span>MARKETS</span><span>WORLD</span><span>VIDEO</span>
      <span>MORE ▾</span>
      <svg width="14" height="14" viewBox="0 0 14 14"><circle cx="6" cy="6" r="4.3" fill="none" stroke="#fff" stroke-width="2"/><line x1="9" y1="9" x2="13" y2="13" stroke="#fff" stroke-width="2"/></svg>
      <span class="signin"><svg width="10" height="12" viewBox="0 0 10 12"><rect x="0" y="5" width="10" height="7" rx="1" fill="#fff"/><path d="M2.5 5V3.5a2.5 2.5 0 0 1 5 0V5" fill="none" stroke="#fff" stroke-width="1.5"/></svg>SIGN IN</span>
    </nav>
  </div>
  <div class="hero-copy">
    <div class="hero-kicker">BUSINESS AND TECH</div>
    <div class="hero-title">AT VERO EOS ET ACCUSAMUS ET</div>
    <p class="hero-text">Nam libero tempore, cum soluta nobis est eligendi optio cumque nihil impedit quo<br>minus id quod maxime placeat facere possimus, omnis</p>
    <span class="hero-btn">GET MORE INFO</span>
  </div>
  <div class="dots"><span class="on"></span><span></span><span></span><span></span></div>
</header>

<section class="section" style="top:590px">
  <h2 class="section-title">FEATURED NEWS</h2>
  <div class="section-body">
    <article class="lead">
      <div class="lead-photo" role="img" aria-label="Businessmen reading a tablet in an office" style="background:linear-gradient(120deg,#6d7a88,#b9c3cc 50%,#4a5561)"></div>
      <div class="lead-shade"></div>
      <div class="lead-copy">
        <div class="lead-kicker">BUSINESS AND TECH</div>
        <div class="lead-title">AT VERO EOS ET ACCUSAMUS ET</div>
        <p class="lead-text">Nam libero tempore, cum soluta nobis est eligendi optio cumque nihil impedit quo minus id quod maxime placeat facere possimus, omnis</p>
        <div class="meta"><svg viewBox="0 0 10 10"><rect x="0" y="1" width="10" height="9"/></svg>22/04/2017<span class="sep">|</span><svg viewBox="0 0 10 10"><circle cx="5" cy="3" r="2.5"/><path d="M0 10a5 5 0 0 1 10 0z"/></svg>John</div>
      </div>
    </article>
    <div class="list">
      <article class="item">
        <div class="thumb"><div class="thumb-photo" role="img" aria-label="Desk with business papers" style="background:linear-gradient(135deg,#e9ecef,#9aa3ad)"></div></div>
        <div class="item-copy"><div class="item-kicker">Business</div><div class="item-title">At vero eos et accusamus iusto od io dignissimos duci</div><div class="meta"><svg viewBox="0 0 10 10"><rect x="0" y="1" width="10" height="9"/></svg>22/04/2017<span class="sep">|</span><svg viewBox="0 0 10 10"><circle cx="5" cy="3" r="2.5"/><path d="M0 10a5 5 0 0 1 10 0z"/></svg>John</div></div>
      </article>
      <article class="item">
        <div class="thumb"><div class="thumb-photo" role="img" aria-label="Tablet showing charts" style="background:linear-gradient(135deg,#dfe6ee,#7fa6c8)"></div></div>
        <div class="item-copy"><div class="item-kicker">Tech</div><div class="item-title">At vero eos et accusamus iusto od io dignissimos duci</div><div class="meta"><svg viewBox="0 0 10 10"><rect x="0" y="1" width="10" height="9"/></svg>22/04/2017<span class="sep">|</span><svg viewBox="0 0 10 10"><circle cx="5" cy="3" r="2.5"/><path d="M0 10a5 5 0 0 1 10 0z"/></svg>John</div></div>
      </article>
      <article class="item">
        <div class="thumb"><div class="thumb-photo" role="img" aria-label="Pink piggy bank and coins" style="background:linear-gradient(135deg,#f4dfe2,#e29aa6)"></div></div>
        <div class="item-copy"><div class="item-kicker">Money</div><div class="item-title">At vero eos et accusamus iusto od io dignissimos duci</div><div class="meta"><svg viewBox="0 0 10 10"><rect x="0" y="1" width="10" height="9"/></svg>22/04/2017<span class="sep">|</span><svg viewBox="0 0 10 10"><circle cx="5" cy="3" r="2.5"/><path d="M0 10a5 5 0 0 1 10 0z"/></svg>John</div></div>
      </article>
    </div>
  </div>
</section>

<div class="banner" style="top:1137px">
  <div class="banner-photo" role="img" aria-label="Hand with pen over a calculator and financial charts" style="background:linear-gradient(90deg,#5d6670,#a8b1ba 40%,#c9ced3 70%,#9aa2ab)"></div>
  <div class="banner-shade"></div>
  <p class="banner-text">At vero eos et accusamus et iusto odio dignissimos ducimu<br>qui blanditiis praesentium voluptatum deleni</p>
</div>

<section class="section" style="top:1428px">
  <h2 class="section-title">MORE TOP NEWS</h2>
  <div class="section-body">
    <article class="lead">
      <div class="lead-photo" role="img" aria-label="Two colleagues discussing work at a laptop" style="background:linear-gradient(120deg,#5a6470,#a9aeb2 45%,#2f3740)"></div>
      <div class="lead-shade"></div>
      <div class="lead-copy">
        <div class="lead-kicker">BUSINESS AND TECH</div>
        <div class="lead-title">AT VERO EOS ET ACCUSAMUS ET</div>
        <p class="lead-text">Nam libero tempore, cum soluta nobis est eligendi optio cumque nihil impedit quo minus id quod maxime placeat facere possimus, omnis</p>
        <div class="meta"><svg viewBox="0 0 10 10"><rect x="0" y="1" width="10" height="9"/></svg>22/04/2017<span class="sep">|</span><svg viewBox="0 0 10 10"><circle cx="5" cy="3" r="2.5"/><path d="M0 10a5 5 0 0 1 10 0z"/></svg>John</div>
      </div>
    </article>
    <div class="list">
      <article class="item">
        <div class="thumb"><div class="thumb-photo" role="img" aria-label="Digital market network graphic" style="background:linear-gradient(135deg,#0d2345,#2f6fb0)"></div></div>
        <div class="item-copy"><div class="item-kicker">Markets</div><div class="item-title">At vero eos et accusamus iusto od io dignissimos duci</div><div class="meta"><svg viewBox="0 0 10 10"><rect x="0" y="1" width="10" height="9"/></svg>22/04/2017<span class="sep">|</span><svg viewBox="0 0 10 10"><circle cx="5" cy="3" r="2.5"/><path d="M0 10a5 5 0 0 1 10 0z"/></svg>John</div></div>
      </article>
      <article class="item">
        <div class="thumb"><div class="thumb-photo" role="img" aria-label="Hands typing on a laptop" style="background:linear-gradient(135deg,#3e4752,#c4c9ce)"></div></div>
        <div class="item-copy"><div class="item-kicker">Technology</div><div class="item-title">At vero eos et accusamus iusto od io dignissimos duci</div><div class="meta"><svg viewBox="0 0 10 10"><rect x="0" y="1" width="10" height="9"/></svg>22/04/2017<span class="sep">|</span><svg viewBox="0 0 10 10"><circle cx="5" cy="3" r="2.5"/><path d="M0 10a5 5 0 0 1 10 0z"/></svg>John</div></div>
      </article>
      <article class="item">
        <div class="thumb"><div class="thumb-photo" role="img" aria-label="Businessman walking in a busy street" style="background:linear-gradient(135deg,#c8b9a6,#5e5750)"></div></div>
        <div class="item-copy"><div class="item-kicker">Money</div><div class="item-title">At vero eos et accusamus iusto od io dignissimos duci</div><div class="meta"><svg viewBox="0 0 10 10"><rect x="0" y="1" width="10" height="9"/></svg>22/04/2017<span class="sep">|</span><svg viewBox="0 0 10 10"><circle cx="5" cy="3" r="2.5"/><path d="M0 10a5 5 0 0 1 10 0z"/></svg>John</div></div>
      </article>
    </div>
  </div>
</section>

<div class="banner" style="top:1977px">
  <div class="banner-photo" role="img" aria-label="Pen over printed line charts" style="background:linear-gradient(90deg,#8d959e,#c7ccd1 45%,#dcdfe2 70%,#b5bcc3)"></div>
  <div class="banner-shade"></div>
  <p class="banner-text">At vero eos et accusamus et iusto odio dignissimos ducimu<br>qui blanditiis praesentium voluptatum deleni</p>
</div>

<section class="section" style="top:2264px">
  <h2 class="section-title">FEATURED VIDEO</h2>
  <div class="section-body">
    <article class="lead">
      <div class="lead-photo" role="img" aria-label="Silhouetted business people by large office windows" style="background:linear-gradient(180deg,#a9c2d6 0%,#d8e2ea 45%,#3c3a38 75%,#1d1b1a 100%)"></div>
      <svg class="play" width="62" height="62" viewBox="0 0 62 62"><circle cx="31" cy="31" r="29" fill="rgba(0,0,0,.45)" stroke="#fff" stroke-width="2.5"/><path d="M25 19l19 12-19 12z" fill="#fff"/></svg>
    </article>
    <div class="list">
      <article class="item">
        <div class="thumb"><div class="thumb-photo" role="img" aria-label="Speaker at a press event" style="background:linear-gradient(135deg,#c9d6e2,#7b8c9c)"></div><svg class="play" width="34" height="34" viewBox="0 0 34 34"><circle cx="17" cy="17" r="16" fill="rgba(0,0,0,.45)" stroke="#fff" stroke-width="1.5"/><path d="M13 10l11 7-11 7z" fill="#fff"/></svg></div>
        <div class="item-copy"><div class="item-kicker">Politics</div><div class="item-title">At vero eos et accusamus iusto od io dignissimos duci</div><div class="meta"><svg viewBox="0 0 10 10"><rect x="0" y="1" width="10" height="9"/></svg>22/04/2017<span class="sep">|</span><svg viewBox="0 0 10 10"><circle cx="5" cy="3" r="2.5"/><path d="M0 10a5 5 0 0 1 10 0z"/></svg>John</div></div>
      </article>
      <article class="item">
        <div class="thumb"><div class="thumb-photo" role="img" aria-label="Team working over documents" style="background:linear-gradient(135deg,#2f9fc4,#d9c9a8)"></div><svg class="play" width="34" height="34" viewBox="0 0 34 34"><circle cx="17" cy="17" r="16" fill="rgba(0,0,0,.45)" stroke="#fff" stroke-width="1.5"/><path d="M13 10l11 7-11 7z" fill="#fff"/></svg></div>
        <div class="item-copy"><div class="item-kicker">Deals</div><div class="item-title">At vero eos et accusamus iusto od io dignissimos duci</div><div class="meta"><svg viewBox="0 0 10 10"><rect x="0" y="1" width="10" height="9"/></svg>22/04/2017<span class="sep">|</span><svg viewBox="0 0 10 10"><circle cx="5" cy="3" r="2.5"/><path d="M0 10a5 5 0 0 1 10 0z"/></svg>John</div></div>
      </article>
      <article class="item">
        <div class="thumb"><div class="thumb-photo" role="img" aria-label="Group meeting in a bright room" style="background:linear-gradient(135deg,#e6dcd0,#8f7a66)"></div><svg class="play" width="34" height="34" viewBox="0 0 34 34"><circle cx="17" cy="17" r="16" fill="rgba(0,0,0,.45)" stroke="#fff" stroke-width="1.5"/><path d="M13 10l11 7-11 7z" fill="#fff"/></svg></div>
        <div class="item-copy"><div class="item-kicker">Entertainment</div><div class="item-title">At vero eos et accusamus iusto od io dignissimos duci</div><div class="meta"><svg viewBox="0 0 10 10"><rect x="0" y="1" width="10" height="9"/></svg>22/04/2017<span class="sep">|</span><svg viewBox="0 0 10 10"><circle cx="5" cy="3" r="2.5"/><path d="M0 10a5 5 0 0 1 10 0z"/></svg>John</div></div>
      </article>
    </div>
  </div>
</section>

<div class="banner" style="top:2810px">
  <div class="banner-photo" role="img" aria-label="Person in a checked shirt holding a tablet" style="background:linear-gradient(90deg,#b0a7a2,#cfc6c2 40%,#a38d88 70%,#7c6a66)"></div>
  <div class="banner-shade"></div>
  <p class="banner-text">At vero eos et accusamus et iusto odio dignissimos ducimu<br>qui blanditiis praesentium voluptatum deleni</p>
</div>

<footer class="footer">
  <div class="fcol" style="left:100px"><h4>Information</h4><ul><li>About Us</li><li>Careers</li><li>Privacy &amp; Security</li><li>Site Map</li><li>Terms of Use</li><li>Blog</li></ul></div>
  <div class="fcol" style="left:256px"><h4>Tech</h4><ul><li>Business</li><li>Culture</li><li>Gadgets</li><li>Future</li><li>Startups</li></ul></div>
  <div class="fcol" style="left:362px"><h4>Money</h4><ul><li>Business</li><li>Markets</li><li>Tech</li><li>Luxury</li></ul></div>
  <div class="fcol" style="left:485px"><h4>Entertainment</h4><ul><li>Stars</li><li>Screen</li><li>Binge</li><li>Culture</li><li>Media</li></ul></div>
  <div class="fcol" style="left:654px"><h4>Features</h4><ul><li>Video news</li><li>Feature shows</li><li>NWL</li><li>TV shows</li><li>TV schedule</li></ul></div>
  <div class="fcol subscribe" style="left:777px">
    <h4>Email Subscription</h4>
    <p>Register your email address to get information about us</p>
    <div class="sub-form"><span class="sub-input">Email Address</span><span class="sub-btn">SUBSCRIBE</span></div>
    <div class="connect">Stay Connected</div>
    <div class="socials"><span></span><span></span><span></span><span></span><span></span><span></span><span></span><span></span></div>
  </div>
  <div class="footer-rule"></div>
  <p class="copyright">Copyrights © 2017, Tidewell News. All Rights Reserved &nbsp;|&nbsp; Privacy Policy | Terms of Use | Feedback</p>
</footer>

</body>
</html>
```